Las Vegas Tour guide needs website of future for physical and selfguided assets

Neon Drifters is the parent site to my Las Vegas tour operation. Within this is a physical walking tour called Whispers and the Racket, the site traffic driver where I tell history with a paranormal twist. The legacy site can be seen at spookyroutewalks.com.
The Neon Drifters app has self guided tours called Desert Hop Trail/Whispers and The Racket Retold/Calloway Row Stroll. Rivano is a 3rd party tour company I have partnered with to sale self-guided tours with a scavenger hunt theme.
I like black and pink and pistachio green colors however am flexible in theme. Colors should follow Vegas 50-60s aesthetics. The “Greetings From Silver Gulch Marker” should not be considered as design inspiration. 95% of traffic is on mobile. Final design should be easy to understand guided versus self-guided option. Show cross promotion links for digital assets/physical tour. Rivano content tbd by end of week 9 Aug 2021
sites i like
nationalspiritstrolls.com
heronsandshades.com
oldportphantomtrips.net
Updates

Needs a book now at top, or floating like lorvantrips. Less busy and stay away from using photos. I have included more websites for inspiration. I would like a mashup of the two sites eerieechoplace and lorvantrips. I am unsure what some of your designs would look like on a mobile screen. Please screenshot that. https://eerieechoplace.com/ https://www.lorvantrips.com/ https://k7vrx.com/ https://bqspecters.com/ https://bluefinjaunts.com/tours/new-york-city/shades-of-pellham-corner/

Family member hospitalized need extra time to review

Target Market(s)

Tourist 25+

Industry/Entity Type

Travel. Tour guide.

Coding

Coded - Design and coding required

Number of Pages Required

5+ page

Font styles to use
Serif

Colors
00AB8E
00BBA5
67D7C9
C6EFE9
E9F9F6
59FF00
82FF00
B8FF75
E3FFCB
F4FFEA
EB3D1F
EC4F4E
F09395
F8D3D4
FCEDEE
E54698
E96AAD
F1A4CE
F9D9EA
FCEFF6

Requirements
Must have
• Cross promotion between physical tour and digital
Nice to have
• sliver button like ads as breaks between tour info
Should not have
• "Greetings from Silver Gulch Marker". no photos. no animation.

```html
<!DOCTYPE html>
<html lang="en">
<head>
<meta charset="utf-8">
<title>Calloway Row Walking Tour</title>
<link href="https://fonts.googleapis.com/css2?family=Federant&family=Montserrat:wght@400;500;700&family=Mulish:wght@400;600&display=swap" rel="stylesheet">
<style>
:root{
  --ink:#111;
  --orange:#E8891A;
  --flame:#E85A0E;
  --brown:#7A2E1E;
  --pistachio:#DEDF99;
  --lime:#A8C93A;
  --cyan:#3FE3E0;
  --green:#1E9A5A;
  --body:#444;
  --white:#fff;
  --line:#555;
}
*{margin:0;padding:0;box-sizing:border-box}
html,body{width:1200px;height:2670px;overflow:hidden;background:var(--white)}
body{position:relative;font-family:'Mulish',sans-serif;color:var(--body)}
.abs{position:absolute}
.display{font-family:'Federant',serif;font-weight:400}
.hero-art{left:0;top:0;width:1200px;height:660px}
.nav{top:24px;right:180px;display:flex;gap:22px;font-family:'Montserrat',sans-serif;font-size:14px;font-weight:500;color:var(--white);white-space:nowrap}
.brand{left:142px;top:20px;width:220px;text-align:center}
.brand-mark{width:110px;height:110px;border-radius:50%;background:var(--orange);margin:0 auto 14px}
.brand-name{font-family:'Federant',serif;font-size:30px;color:var(--orange);line-height:1;white-space:nowrap}
.hero-title{left:0;width:1200px;top:244px;text-align:center;font-size:40px;line-height:64px;color:var(--white)}
.hero-sub{left:0;width:1200px;top:370px;text-align:center;font-family:'Montserrat',sans-serif;font-size:18px;font-weight:500;color:var(--white)}
.hero-note{left:0;width:1200px;top:400px;text-align:center;font-family:'Montserrat',sans-serif;font-size:18px;font-weight:500;color:#F0A818}
.section-title{left:0;width:1200px;text-align:center;font-size:42px;color:var(--brown)}
.section-title .accent{color:var(--orange)}
.about-title{top:742px}
.about-text{left:176px;width:850px;top:817px;text-align:center;font-size:14px;line-height:25.4px}
.tour{top:1015px;width:290px;text-align:center}
.tour-img{width:290px;height:290px;border-radius:50%}
.tour-name{margin:40px -40px 0;font-family:'Montserrat',sans-serif;font-size:23px;line-height:30px;color:#222;white-space:nowrap}
.tour-name.single{margin-top:36px}
.reviews{left:0;top:1492px;width:1200px;height:440px;background:var(--pistachio)}
.reviews-title{top:1577px}
.card{top:1668px;width:283px;height:171px;background:var(--white);border-radius:0 0 22px 0;box-shadow:2px 3px 0 rgba(0,0,0,.08);padding:14px 19px 0}
.stars{color:#F4A300;font-size:12px;letter-spacing:1px}
.quote-mark{position:absolute;right:22px;top:-38px;font-family:'Federant',serif;font-size:110px;line-height:1;color:var(--flame)}
.card p{margin-top:12px;font-size:12.4px;line-height:21px;color:#555}
.card .who{margin-top:16px;font-family:'Montserrat',sans-serif;font-weight:700;font-size:13px;color:#222}
.arrow{top:1735px;width:34px;height:34px;border-radius:50%;display:flex;align-items:center;justify-content:center}
.arrow.prev{left:70px;background:var(--white)}
.arrow.next{left:1096px;background:var(--green)}
.cta{top:2012px;line-height:64px}
.footer-art{left:0;top:2200px;width:1200px;height:470px}
.follow-row{left:310px;top:2343px;height:35px;display:flex;align-items:center;gap:10px}
.follow{font-size:20px;color:var(--cyan);white-space:nowrap;margin-right:10px}
.social{width:35px;height:35px;background:#1f1f1f;display:flex;align-items:center;justify-content:center}
.social span{width:14px;height:14px;background:var(--white);border-radius:2px}
.contact{top:2417px;width:213px;height:154px;border:1px solid var(--line);text-align:center;color:var(--white);font-family:'Montserrat',sans-serif}
.contact svg{margin-top:24px}
.contact .label{margin-top:6px;font-size:15px}
.contact .value{margin-top:4px;font-size:13.5px}
.foot-brand{left:855px;top:2340px;width:210px;text-align:center}
.foot-brand .brand-mark{width:120px;height:120px}
.rule{left:146px;top:2598px;width:920px;height:1px;background:#333}
.copy{left:0;width:1200px;top:2627px;text-align:center;font-family:'Montserrat',sans-serif;font-size:12px;color:#ddd}
</style>
</head>
<body>

<svg class="abs hero-art" viewBox="0 0 1200 660" role="img" aria-label="Dark night city skyline photograph">
  <defs>
    <linearGradient id="sky" x1="0" y1="0" x2="0" y2="1">
      <stop offset="0" stop-color="#3a3a3a"/>
      <stop offset="0.5" stop-color="#4a4a4a"/>
      <stop offset="1" stop-color="#2a2a2a"/>
    </linearGradient>
  </defs>
  <path d="M0,520 C90,640 260,660 450,655 C720,648 980,560 1200,440 L1200,470 C980,585 720,665 450,668 C250,670 80,650 0,560 Z" fill="#B23A0A"/>
  <path d="M0,505 C90,625 260,650 450,645 C720,638 980,550 1200,428 L1200,455 C980,575 720,655 450,658 C250,660 80,640 0,545 Z" fill="var(--flame)"/>
  <path d="M0,0 H1200 V428 C980,550 720,638 450,645 C260,650 90,625 0,505 Z" fill="url(#sky)"/>
  <circle cx="200" cy="70" r="232" fill="#000" opacity=".25"/>
  <circle cx="1185" cy="30" r="75" fill="#1a1a1a" opacity=".6"/>
  <circle cx="1195" cy="20" r="55" fill="#e5e5e5"/>
</svg>

<nav class="abs nav">
  <span>Whispers And The Racket Las Vegas Walking Tour</span>
  <span>Desert Hop Trail</span>
  <span>Neon Drifters</span>
</nav>

<div class="abs brand">
  <div class="brand-mark"></div>
  <div class="brand-name">Calloway Row</div>
</div>

<h1 class="abs hero-title display">Desert Hop Trail/Whispers and The Racket<br>Retold/Calloway Row Stroll.</h1>
<p class="abs hero-sub">Show&nbsp; Cross Promotion Links For Digital Assets/physical Tour.</p>
<p class="abs hero-note">Rivano Content Tbd By End of Week 9 Aug 2021</p>

<h2 class="abs section-title about-title display"><span class="accent">About Calloway Row</span> Walking Tour</h2>
<p class="abs about-text">Lorem ipsum dolor sit amet, consectetuer adipiscing elit, sed diam nonummy nibh euismod tincidunt ut laoreet dolore magna aliquam erat volutpat. Ut wisi enim ad minim veniam, quis nostrud exerci tation ullamcorper suscipit lobortis nisl ut aliquip ex ea commodo consequat. Duis autem vel eum iriure dolor in hendrerit in vulputate velit esse molestie consequat, vel illum dolore eu feugiat nulla facilisis at vero eros et accumsan et iusto odio dignissim qui blandit praesent luptatum zzril delenit augue duis dolore te feugait nulla facilisi.</p>

<div class="abs tour" style="left:141px">
  <div class="tour-img" role="img" aria-label="Vintage night street photograph for the walking tour" style="background:radial-gradient(circle at 60% 55%,#c9d3a8,#2a3266 70%)"></div>
  <div class="tour-name">Whispers And The Racket<br>Las Vegas Walking Tour</div>
</div>
<div class="abs tour" style="left:455px">
  <div class="tour-img" role="img" aria-label="Row of craft beer glasses photograph" style="background:linear-gradient(90deg,#3a1d10,#c07a20 30%,#8a3a18 50%,#e0b040 70%,#4a2a12)"></div>
  <div class="tour-name single">Desert Hop Trail</div>
</div>
<div class="abs tour" style="left:768px">
  <div class="tour-img" role="img" aria-label="Roadside marker sign at night photograph" style="background:radial-gradient(circle at 45% 50%,#f2e4c0,#d0602a 45%,#2a4a8a 85%)"></div>
  <div class="tour-name single">Neon Drifters</div>
</div>

<section class="abs reviews"></section>
<h2 class="abs section-title reviews-title display"><span class="accent">Customer</span> Reviews</h2>

<div class="abs arrow prev"><svg width="12" height="12" viewBox="0 0 12 12"><path d="M8 1 L3 6 L8 11" stroke="#222" stroke-width="2" fill="none"/></svg></div>
<div class="abs arrow next"><svg width="12" height="12" viewBox="0 0 12 12"><path d="M4 1 L9 6 L4 11" stroke="#fff" stroke-width="2" fill="none"/></svg></div>

<article class="abs card" style="left:143px">
  <span class="quote-mark">”</span>
  <div class="stars">★★★★★</div>
  <p>“Lorem ipsum dolor sit amet, consectetur ipsum dolor sit amet, consectetur&nbsp; lodr adipiscing elit. Sed vel alique ellentesque justo. Mauris est tortor.”</p>
  <div class="who">Jonah Brell</div>
</article>
<article class="abs card" style="left:459px">
  <span class="quote-mark">”</span>
  <div class="stars">★★★★★</div>
  <p>“Lorem ipsum dolor sit amet, consectetur ipsum dolor sit amet, consectetur&nbsp; lodr adipiscing elit. Sed vel alique ellentesque justo. Mauris est tortor.”</p>
  <div class="who">Liam AM</div>
</article>
<article class="abs card" style="left:776px">
  <span class="quote-mark">”</span>
  <div class="stars">★★★★★</div>
  <p>“Lorem ipsum dolor sit amet, consectetur ipsum dolor sit amet, consectetur&nbsp; lodr adipiscing elit. Sed vel alique ellentesque justo. Mauris est tortor.”</p>
  <div class="who">William WM</div>
</article>

<h2 class="abs section-title cta display"><span class="accent">Buy tickets online or</span><br>give us a call at 1-800-555-0147</h2>

<svg class="abs footer-art" viewBox="0 0 1200 470">
  <path d="M0,238 C250,60 560,10 800,14 C1000,18 1140,70 1200,118 L1200,470 L0,470 Z" fill="var(--lime)"/>
  <path d="M0,248 C250,75 560,26 800,30 C1000,34 1140,88 1200,140 L1200,470 L0,470 Z" fill="var(--ink)"/>
</svg>

<div class="abs follow-row">
  <div class="follow display">Follow us @ callowayrow</div>
  <div class="social"><span></span></div>
  <div class="social"><span></span></div>
  <div class="social"><span></span></div>
  <div class="social"><span></span></div>
</div>

<div class="abs contact" style="left:143px">
  <svg width="34" height="46" viewBox="0 0 34 46"><path d="M17 44 C17 44 3 26 3 16 A14 14 0 0 1 31 16 C31 26 17 44 17 44 Z" fill="none" stroke="var(--orange)" stroke-width="2.4"/><circle cx="17" cy="16" r="5.5" fill="none" stroke="var(--orange)" stroke-width="2.4"/></svg>
  <div class="label">Address</div>
  <div class="value">Calloway Row Stroll</div>
</div>
<div class="abs contact" style="left:379px">
  <svg width="44" height="44" viewBox="0 0 44 44"><path d="M9 5 L16 5 L19 14 L14 18 C17 25 20 28 26 31 L30 26 L39 29 L39 36 C39 38 37 40 35 40 C19 39 5 25 4 9 C4 7 6 5 9 5 Z" fill="none" stroke="var(--orange)" stroke-width="2.2"/><path d="M25 6 A13 13 0 0 1 38 19 M25 12 A7 7 0 0 1 32 19" fill="none" stroke="var(--orange)" stroke-width="2.2"/></svg>
  <div class="label">Phone</div>
  <div class="value">123.456.7899</div>
</div>
<div class="abs contact" style="left:615px">
  <svg width="46" height="44" viewBox="0 0 46 44"><path d="M3 18 L23 4 L43 18 L43 41 L3 41 Z" fill="none" stroke="var(--orange)" stroke-width="2.2"/><path d="M3 18 L23 31 L43 18 M3 41 L18 28 M43 41 L28 28" fill="none" stroke="var(--orange)" stroke-width="2.2"/><rect x="10" y="11" width="26" height="13" fill="none" stroke="var(--orange)" stroke-width="2"/></svg>
  <div class="label">Email</div>
  <div class="value">inquiry@callowayrow.com</div>
</div>

<div class="abs foot-brand">
  <div class="brand-mark"></div>
  <div class="brand-name">Calloway Row</div>
</div>

<div class="abs rule"></div>
<p class="abs copy">© 2021 Calloway Row Walking Tour. All Rights Reserved.</p>

</body>
</html>
```